Realty Group Needs Classy, Contemporary Letterhead Design

We need a letterhead design for a new realty company located in NY, USA. We buy investment properties to rehabilitate and or keep in our rental portfolio.

```html
<!DOCTYPE html>
<html lang="en">
<head>
<meta charset="utf-8">
<title>Meridian Realty Group — Letterhead</title>
<link rel="stylesheet" href="https://fonts.googleapis.com/css2?family=Roboto:wght@500;700;900&family=Arimo:wght@400&family=Great+Vibes&display=swap">
<style>
  :root {
    --brand-purple: #4a1f86;
    --ink-dark: #222222;
    --ink-mid: #5a5a5a;
    --ink-body: #6b6b6b;
    --rule-grey: #777777;
    --paper: #ffffff;
    --backdrop: #f4f4f4;
    --watermark: #ececec;
    --footer-band: #eeeeee;
  }
  * { box-sizing: border-box; margin: 0; padding: 0; }
  html, body { width: 788px; height: 1200px; overflow: hidden; }
  body { background: var(--backdrop); position: relative; font-family: "Arimo", Arial, sans-serif; }

  .letterhead {
    position: absolute; left: 28px; top: 126px;
    width: 732px; height: 948px;
    background: var(--paper);
    box-shadow: 0 2px 10px rgba(0,0,0,0.18);
    overflow: hidden;
  }
  .background-pattern {
    position: absolute; left: 180px; top: 150px; width: 552px; height: 560px;
    background: radial-gradient(ellipse at 50% 40%, rgba(235,235,235,0.55), rgba(255,255,255,0) 70%);
  }

  .brand {
    position: absolute; left: 41px; top: 64px; width: 330px;
    font-family: "Roboto", Arial, sans-serif; font-weight: 900;
    color: var(--brand-purple);
  }
  .brand-name { font-size: 60px; line-height: 60px; letter-spacing: 1px; }
  .brand-sub {
    font-size: 17px; line-height: 20px; letter-spacing: 1px;
    margin-top: -6px; text-align: center;
  }

  .contact {
    position: absolute; left: 478px; top: 32px; width: 240px; height: 110px;
  }
  .contact-arrow { position: absolute; left: 0; top: 0; }
  .contact-list { position: absolute; left: 34px; top: 0; list-style: none; }
  .contact-item {
    position: relative; display: flex; align-items: flex-start;
    font-family: "Roboto", Arial, sans-serif; font-weight: 700;
    font-size: 12.5px; line-height: 13px; color: var(--ink-mid);
    margin-bottom: 13px;
  }
  .contact-item svg { flex: none; width: 17px; height: 17px; margin-right: 11px; margin-top: -1px; }

  .letter-meta, .recipient, .closing-line {
    position: absolute; left: 42px;
    font-family: "Roboto", Arial, sans-serif; font-weight: 500;
    font-size: 12.5px; color: var(--ink-mid);
  }
  .letter-meta { top: 214px; }
  .recipient { top: 261px; line-height: 19.5px; font-style: normal; }
  .salutation {
    position: absolute; left: 42px; top: 348px;
    font-family: "Roboto", Arial, sans-serif; font-weight: 700;
    font-size: 16px; color: var(--ink-dark);
  }
  .letter-body { position: absolute; left: 42px; top: 380px; width: 652px; }
  .letter-body p {
    font-size: 13px; line-height: 15.8px; color: var(--ink-body);
    margin-bottom: 15.6px;
  }
  .closing-line { top: 732px; }
  .signature {
    position: absolute; left: 42px; top: 764px;
    font-family: "Great Vibes", cursive; font-size: 27px; color: var(--brand-purple);
  }

  .watermark {
    position: absolute; left: 216px; top: 854px;
    font-family: "Roboto", Arial, sans-serif; font-weight: 900;
    font-size: 84px; line-height: 84px; letter-spacing: 4px;
    color: var(--watermark);
  }
  .footer-band {
    position: absolute; left: 0; bottom: 0; width: 100%; height: 23px;
    background: var(--footer-band);
  }
</style>
</head>
<body>
  <main class="letterhead">
    <div class="background-pattern" role="img" aria-label="Faint grey diamond pattern in the letter background"></div>

    <header>
      <div class="brand">
        <div class="brand-name">MERIDIAN</div>
        <div class="brand-sub">Realty Group, LLC</div>
      </div>

      <div class="contact">
        <svg class="contact-arrow" width="20" height="106" viewBox="0 0 20 106" aria-hidden="true">
          <polygon points="10,2 19,15 1,15" fill="var(--rule-grey)"/>
          <rect x="8.5" y="14" width="3" height="92" fill="var(--rule-grey)"/>
        </svg>
        <ul class="contact-list">
          <li class="contact-item" style="margin-bottom:8px">
            <svg viewBox="0 0 20 20" aria-hidden="true"><circle cx="10" cy="10" r="10" fill="var(--brand-purple)"/><path d="M10 4.5a3.6 3.6 0 0 0-3.6 3.6c0 2.7 3.6 6.6 3.6 6.6s3.6-3.9 3.6-6.6A3.6 3.6 0 0 0 10 4.5z" fill="#fff"/><circle cx="10" cy="8.1" r="1.4" fill="var(--brand-purple)"/></svg>
            <span>Your address goes here,<br>Street here</span>
          </li>
          <li class="contact-item">
            <svg viewBox="0 0 20 20" aria-hidden="true"><circle cx="10" cy="10" r="10" fill="var(--brand-purple)"/><path d="M7 5.2l1.6-.3 1.1 2.5-1 .9c.5 1.2 1.4 2.1 2.6 2.7l.9-1 2.5 1.1-.3 1.6c-.2.7-.9 1.1-1.6 1-3.4-.6-5.9-3.2-6.5-6.5-.1-.7.3-1.4.7-2z" fill="#fff"/></svg>
            <span>+0 000 0000 000</span>
          </li>
          <li class="contact-item">
            <svg viewBox="0 0 20 20" aria-hidden="true"><circle cx="10" cy="10" r="10" fill="var(--brand-purple)"/><rect x="5" y="6.5" width="10" height="7" rx="1" fill="#fff"/><path d="M5.3 7l4.7 3.6L14.7 7" fill="none" stroke="var(--brand-purple)" stroke-width="1"/></svg>
            <span>Your@mail.com</span>
          </li>
          <li class="contact-item">
            <svg viewBox="0 0 20 20" aria-hidden="true"><circle cx="10" cy="10" r="10" fill="var(--brand-purple)"/><circle cx="10" cy="10" r="5" fill="none" stroke="#fff" stroke-width="1.3"/><ellipse cx="10" cy="10" rx="2" ry="5" fill="none" stroke="#fff" stroke-width="1.1"/><line x1="5" y1="10" x2="15" y2="10" stroke="#fff" stroke-width="1.1"/></svg>
            <span>Yourwebsite.com</span>
          </li>
        </ul>
      </div>
    </header>

    <p class="letter-meta">Date here, Year</p>
    <address class="recipient">First Last Name<br>Street Address<br>City, State 0000</address>

    <h1 class="salutation">Dear Sir/ Madam,</h1>

    <section class="letter-body">
      <p>Lorem Ipsum is simply dummy text of the printing and typesetting industry. Lorem Ipsum has been the industry's standard dummy text ever since the 1500s, when an unknown printer took a galley of type and scrambled it to make a type specimen book.</p>
      <p>It has survived not only five centuries, but also the leap into electronic typesetting, essentially unchanged.<br>It was popularised in the 1960s with the release of Lettergrid sheets containing Lorem Ipsum passages, &amp; more recently with desktop publishing software like Folio Layout Studio including versions of Lorem Ipsum.</p>
      <p>It is a long established fact that a reader will be distracted by the readable content of a page when looking at its layout. The point of using Lorem Ipsum is that it has a more-or-less normal distribution of letters, as opposed to using 'Content here, content here', making it look like readable English. Many desktop publishing packages and web page editors now use Lorem Ipsum as their default model text, and a search for 'lorem ipsum' will uncover many web sites still in their infancy. Various versions have evolved over the years, sometimes by accident, sometimes on purpose injected humour and the like.</p>
      <p>All the Lorem Ipsum generators on the Internet tend to repeat predefined chunks as necessary, making this the first true generator on the Internet. It uses a dictionary of over 200 Latin words, combined with a handful of model sentence structures, to generate Lorem Ipsum which looks reasonable. The generated Lorem Ipsum is therefore always free from repetition, injected humour, or non-characteristic words etc.</p>
    </section>

    <p class="closing-line">Your Sincerely,</p>
    <p class="signature">John</p>

    <div class="watermark" aria-hidden="true">MERIDIAN</div>
    <div class="footer-band"></div>
  </main>
</body>
</html>
```